Velorin Health is a Direct primary office that needs a great flyer design

Velorin Health has been rebranded with a new logo and website and need new flyers to fit in with our new model and direction. Please refer to velorin-example.com for content. Attached is a possible layout.

```html
<!DOCTYPE html>
<html lang="en">
<head>
<meta charset="utf-8">
<title>Velorin Health – Direct Primary Care Brochure</title>
<link href="https://fonts.googleapis.com/css2?family=Roboto:wght@400;500;700&display=swap" rel="stylesheet">
<style>
:root{
  --green:#12893d;
  --green-dark:#0b6b35;
  --navy:#0c1456;
  --blue:#1b2f9a;
  --ink:#222;
  --ice:#e6f5fb;
  --bg:#5b5b5b;
  --white:#fff;
}
*{box-sizing:border-box;margin:0;padding:0}
html,body{width:1200px;height:903px;overflow:hidden}
body{background:var(--bg);font-family:'Roboto',Arial,sans-serif;color:var(--ink)}
.spread{position:absolute;left:34px;top:15px;width:1132px;height:873px;display:flex}
.panel{position:relative;height:100%;overflow:hidden}
.panel--inside{width:375px;background:var(--white)}
.panel--contact{width:372px;background:linear-gradient(180deg,var(--green) 0%,#0d6a4a 40%,var(--navy) 78%,var(--navy) 100%);color:var(--white);text-align:center}
.panel--cover{width:385px;background:var(--white);text-align:center}
.photo{position:absolute}
.brand-name{font-family:'Roboto',Arial,sans-serif;font-weight:500;letter-spacing:1px;text-transform:uppercase}

/* inside panel */
.inside-photo{left:0;top:0;width:375px;height:320px;background:linear-gradient(135deg,#e7ecef,#c9d2d8 60%,#8ea3bd)}
.inside-curve{position:absolute;left:0;top:272px}
.badge{position:absolute;left:232px;top:258px;width:100px;height:100px;border-radius:50%;background:var(--navy);border:5px solid var(--white);box-shadow:0 0 0 2px var(--blue)}
.why{position:absolute;left:40px;top:322px;font-weight:700;font-size:15px;line-height:19px;color:var(--blue)}
.why span{color:var(--green-dark)}
.benefits{position:absolute;left:41px;top:371px;list-style:none;font-size:12.5px;line-height:15px;color:#111}
.benefits li{position:relative;padding-left:16px;margin-bottom:8px;width:290px}
.benefits li::before{content:"";position:absolute;left:0;top:3px;width:9px;height:9px;border-radius:50%;background:var(--blue)}
.benefits li::after{content:"";position:absolute;left:2.5px;top:5px;width:3px;height:4px;border:solid var(--white);border-width:0 1.3px 1.3px 0;transform:rotate(45deg)}
.pricing-box{position:absolute;left:42px;top:520px;width:290px;height:172px;border:1.5px solid var(--navy);border-radius:3px}
.pricing-title{position:absolute;left:42px;top:510px;height:20px;padding:0 14px 0 8px;background:var(--blue);color:var(--white);font-size:12.5px;font-weight:500;line-height:20px;border-radius:0 10px 10px 0}
.price-table{position:absolute;left:50px;top:534px;width:274px;font-size:12.5px;color:#333;border-collapse:collapse}
.price-table td{padding:4px 0;vertical-align:top;line-height:15px}
.price-table td.amt{text-align:right}
.inside-foot{position:absolute;left:0;bottom:0;width:375px;height:164px;background:var(--ice)}
.inside-foot .brand-name{position:absolute;left:0;width:100%;top:33px;text-align:center;color:var(--blue);font-size:26px}
.foot-contact{position:absolute;top:88px;font-size:11px;line-height:15px;color:#222}
.foot-contact--addr{left:40px;padding-left:16px;width:170px}
.foot-contact--web{left:220px;width:150px}
.foot-contact svg{vertical-align:-2px;margin-right:4px}

/* contact panel */
.contact-photo{left:0;top:0;width:372px;height:300px;background:linear-gradient(180deg,rgba(255,255,255,.12),rgba(255,255,255,0))}
.panel--contact .brand-name{position:absolute;left:0;width:100%;top:396px;font-size:34px;color:var(--white)}
.contact-title{position:absolute;left:0;width:100%;top:540px;font-size:26px;font-weight:700;color:#1ed05a;letter-spacing:.5px}
.contact-item{position:absolute;left:0;width:100%;font-size:15.5px;line-height:20px;font-weight:500}
.contact-item svg{display:block;margin:0 auto 6px}

/* cover panel */
.panel--cover .cover-brand{position:absolute;left:0;width:100%;top:60px;font-size:36px;color:var(--blue)}
.cover-photo{left:0;top:140px;width:385px;height:500px;background:linear-gradient(160deg,#f2f3f5,#cfd6df 50%,#8fa5c9 100%)}
.cover-curve{position:absolute;left:0;top:570px}
.cover-tag{position:absolute;left:0;width:100%;top:624px;font-size:25px;font-weight:500;line-height:35px;color:#111}
.cover-tag span{color:var(--green-dark)}
.cover-rule{position:absolute;left:22px;width:340px;top:711px;height:1px;background:#ccc}
.cover-name{position:absolute;left:0;width:100%;top:732px;font-size:31px;font-weight:700;line-height:35px;color:var(--navy)}
.cover-name span{color:var(--green-dark)}
.cover-url{position:absolute;left:0;top:820px;width:100%;height:27px;background:var(--navy);color:var(--white);font-size:14px;font-weight:500;letter-spacing:5px;line-height:27px}
</style>
</head>
<body>
<div class="spread">

  <section class="panel panel--inside">
    <div class="photo inside-photo" role="img" aria-label="Photo of a smiling doctor with a tablet consulting an older male patient"></div>
    <svg class="inside-curve" width="375" height="60" viewBox="0 0 375 60">
      <path d="M0 30 Q190 -8 375 38 L375 60 L0 60Z" fill="var(--white)"/>
      <path d="M0 30 Q190 -8 375 38" fill="none" stroke="var(--green)" stroke-width="4"/>
    </svg>
    <div class="badge" role="img" aria-label="Award badge"></div>
    <h2 class="why">WHY CHOOSE DIRECT<br><span>PRIMARY CARE?</span></h2>
    <ul class="benefits">
      <li>24/7 access to your doctor via telemedicine, text, and phone consultations</li>
      <li>Same day or next day appointments</li>
      <li>Low cost labs</li>
      <li>Wellness planning and health screenings</li>
      <li>Unlimited appointments</li>
    </ul>
    <div class="pricing-box"></div>
    <div class="pricing-title">Direct Primary Care Pricing</div>
    <table class="price-table">
      <tr><td>Enrollment (Individual):</td><td class="amt">$60</td></tr>
      <tr><td>Enrollment (Family):</td><td class="amt">$120</td></tr>
      <tr><td>Monthly Membership:<br>(child added to adult membership)</td><td class="amt">$10</td></tr>
      <tr><td>Monthly Membership (age 19- 49):</td><td class="amt">$60</td></tr>
      <tr><td>Monthly Membership (age 50-64):</td><td class="amt">$75</td></tr>
      <tr><td>Monthly Membership (age 65-up):</td><td class="amt">$95</td></tr>
    </table>
    <div class="inside-foot">
      <div class="brand-name">Velorin Health</div>
      <p class="foot-contact foot-contact--addr">
        <svg width="11" height="12" viewBox="0 0 12 14" style="position:absolute;left:0;top:2px"><path d="M6 1a4 4 0 0 0-4 4c0 3 4 8 4 8s4-5 4-8a4 4 0 0 0-4-4z" fill="none" stroke="#222" stroke-width="1.5"/><circle cx="6" cy="5" r="1.4" fill="#222"/></svg>
        1180 Maple Ridge Parkway<br>Suite C Alderton,<br>GA 30099
      </p>
      <p class="foot-contact foot-contact--web">
        <svg width="10" height="10" viewBox="0 0 10 10"><path d="M2 1l2 2-1 1.5a6 6 0 0 0 2.5 2.5L7 6l2 2-1.5 1.5C4 9 1 6 .5 2.5z" fill="#222"/></svg>555-014-2290<br>
        <svg width="10" height="8" viewBox="0 0 10 8"><rect width="10" height="8" rx="1" fill="#222"/><path d="M0 1l5 3.5L10 1" stroke="#fff" fill="none"/></svg>info@velorin-example.com<br>
        <svg width="10" height="10" viewBox="0 0 10 10"><circle cx="5" cy="5" r="4.5" fill="#222"/></svg>www.velorin-example.com
      </p>
    </div>
  </section>

  <section class="panel panel--contact">
    <div class="photo contact-photo" role="img" aria-label="Faded photo of a doctor holding a patient's hand"></div>
    <div class="brand-name">Velorin Health</div>
    <h2 class="contact-title">CONTACT INFO</h2>
    <p class="contact-item" style="top:603px">
      <svg width="22" height="22" viewBox="0 0 22 22"><circle cx="11" cy="11" r="10" fill="none" stroke="#fff" stroke-width="1.4"/><path d="M11 5a4 4 0 0 0-4 4c0 3 4 7 4 7s4-4 4-7a4 4 0 0 0-4-4z" fill="none" stroke="#fff" stroke-width="1.4"/></svg>
      1180 Maple Ridge Parkway<br>Suite C Alderton, GA 30099
    </p>
    <p class="contact-item" style="top:688px">
      <svg width="22" height="22" viewBox="0 0 22 22"><circle cx="11" cy="11" r="10" fill="none" stroke="#fff" stroke-width="1.4"/><path d="M8 6l2 2-1 1.5a6 6 0 0 0 3.5 3.5L14 12l2 2-1.5 1.5C10 15 7 12 6.5 7.5z" fill="#fff"/></svg>
      555-014-2290
    </p>
    <p class="contact-item" style="top:748px">
      <svg width="22" height="22" viewBox="0 0 22 22"><circle cx="11" cy="11" r="10" fill="none" stroke="#fff" stroke-width="1.4"/><rect x="6" y="7.5" width="10" height="7" rx="1" fill="#fff"/><path d="M6 8l5 3.5L16 8" stroke="var(--navy)" fill="none"/></svg>
      info@velorin-example.com
    </p>
    <p class="contact-item" style="top:808px">
      <svg width="22" height="22" viewBox="0 0 22 22"><circle cx="11" cy="11" r="10" fill="none" stroke="#fff" stroke-width="1.4"/><circle cx="11" cy="11" r="5.5" fill="none" stroke="#fff" stroke-width="1.2"/><path d="M5.5 11h11M11 5.5v11" stroke="#fff" stroke-width="1"/></svg>
      www.velorin-example.com
    </p>
  </section>

  <section class="panel panel--cover">
    <div class="brand-name cover-brand">Velorin Health</div>
    <div class="photo cover-photo" role="img" aria-label="Photo of an older doctor listening to a young woman's heart with a stethoscope"></div>
    <svg class="cover-curve" width="385" height="80" viewBox="0 0 385 80">
      <path d="M0 52 Q190 -10 385 50 L385 80 L0 80Z" fill="var(--white)"/>
      <path d="M0 52 Q190 -10 385 50" fill="none" stroke="var(--green)" stroke-width="5"/>
    </svg>
    <p class="cover-tag">It is Possible to<br><span>Pay less and Get more</span></p>
    <div class="cover-rule"></div>
    <h1 class="cover-name">Velorin Health<br><span>Direct primary Care</span></h1>
    <div class="cover-url">www.velorin-example.com</div>
  </section>

</div>
</body>
</html>
```